iPhone iOS 7 App For Managing Tasks/Photos for Internal Company Use

We need an app design that displays company objectives and task, and provides the interface for employees to complete a task by uploading a photo and adding comments.

Please see attached mock up sketches as a rough guideline

Final delivery of files must contain PSD, and all layers/objects sliced both is PSD and PNG files

Target Market(s)

This is a tool for internal employee use

Industry/Entity Type

It Company

Requirements
Must have
• Must include logo, and match the colour scheme
Use iPhone iOS 7 Style

```html
<!DOCTYPE html>
<html lang="en">
<head>
<meta charset="utf-8">
<title>News – Company App</title>
<link rel="stylesheet" href="https://fonts.googleapis.com/css2?family=Carlito:wght@400;700&family=Open+Sans:wght@400&family=PT+Sans:wght@700&family=Roboto:wght@400;500&display=swap">
<style>
  :root {
    --bg: #a5b7c1;
    --white: #ffffff;
    --brand: #4e747c;
    --brand-dark: #4a6770;
    --panel: #f2f2f2;
    --panel-back: #ebeded;
    --rule: #d9dddd;
    --ink: #2b2b2b;
    --ink-soft: #555a5c;
    --tab-ink: #8a8f91;
    --nav-ring: #52737a;
    --nav-face: #e9eceb;
    --icon: #8f9596;
  }
  * { box-sizing: border-box; margin: 0; padding: 0; }
  html, body { width: 675px; height: 1200px; overflow: hidden; }
  body { background: var(--bg); position: relative; font-family: "Carlito", "Calibri", sans-serif; color: var(--ink); }

  .status-bar { position: absolute; top: 0; left: 0; width: 675px; height: 50px; font-family: "Roboto", sans-serif; font-size: 23px; color: #111; }
  .status-bar .signal { position: absolute; left: 6px; top: 17px; display: flex; gap: 3px; }
  .status-bar .signal i { width: 13px; height: 13px; border-radius: 50%; background: #111; display: block; }
  .status-bar .signal i.off { background: none; border: 1.5px solid #111; }
  .status-bar .carrier { position: absolute; left: 94px; top: 9px; }
  .status-bar .wifi { position: absolute; left: 196px; top: 12px; }
  .status-bar .clock { position: absolute; left: 0; width: 675px; text-align: center; top: 8px; font-size: 24px; font-weight: 500; }
  .status-bar .bt { position: absolute; left: 510px; top: 11px; }
  .status-bar .level { position: absolute; left: 540px; top: 9px; }
  .status-bar .battery { position: absolute; left: 612px; top: 13px; }

  .app-header { position: absolute; top: 50px; left: 0; width: 675px; height: 85px; background: var(--white); box-shadow: 0 3px 5px rgba(0,0,0,.18); display: flex; align-items: center; justify-content: center; gap: 14px; color: var(--brand); font-family: "Carlito", sans-serif; font-weight: 700; font-size: 35px; letter-spacing: .5px; }
  .app-header .brand-dot { width: 16px; height: 16px; border-radius: 50%; background: var(--brand); }

  .tabs { position: absolute; top: 163px; left: 18px; display: flex; gap: 6px; }
  .tab { height: 30px; padding: 0 12px; font-size: 23px; line-height: 30px; border: 1px solid #c9cfd1; border-bottom: none; background: #e4e7e8; color: var(--tab-ink); }
  .tab.is-active { background: var(--panel); color: #6d7375; height: 32px; }

  .panel-back { position: absolute; left: 28px; top: 195px; width: 629px; height: 767px; background: var(--panel-back); border: 1px solid #c5cccf; box-shadow: 0 1px 3px rgba(0,0,0,.15); }
  .news-panel { position: absolute; left: 18px; top: 191px; width: 613px; height: 756px; background: var(--panel); border: 1px solid #c5cccf; box-shadow: 0 1px 3px rgba(0,0,0,.2); overflow: hidden; }

  .news-item { position: absolute; left: 3px; width: 556px; height: 184px; border-bottom: 2px solid var(--rule); }
  .news-item .avatar { position: absolute; left: 19px; width: 98px; height: 98px; border-radius: 50%; }
  .news-item .time { position: absolute; left: 1px; width: 140px; text-align: center; font-size: 23px; line-height: 28px; color: var(--ink-soft); }
  .news-item .name { position: absolute; left: 148px; font-size: 34px; line-height: 40px; font-weight: 400; color: var(--ink); white-space: nowrap; }
  .news-item .excerpt { position: absolute; left: 148px; width: 380px; font-family: "Open Sans", sans-serif; font-size: 13.2px; line-height: 18px; color: var(--ink-soft); }

  .scroll-track { position: absolute; left: 581px; top: 53px; width: 12px; height: 642px; border: 1.5px solid #b9c1c4; border-radius: 6px; }
  .scroll-thumb { position: absolute; left: 581px; top: 359px; width: 12px; height: 84px; background: var(--brand-dark); border-radius: 6px; }

  .tab-bar { position: absolute; left: 0; top: 1040px; width: 675px; height: 160px; }
  .tab-bar svg { position: absolute; left: 0; top: 0; }
  .tab-bar .label { position: absolute; top: 102px; width: 160px; text-align: center; font-family: "PT Sans", sans-serif; font-weight: 700; font-size: 27px; color: var(--brand-dark); }
</style>
</head>
<body>
  <div class="status-bar">
    <div class="signal"><i></i><i></i><i></i><i class="off"></i><i class="off"></i></div>
    <span class="carrier">OSKELTA</span>
    <svg class="wifi" width="26" height="20" viewBox="0 0 26 20"><path d="M13 19 L2 7 A16 16 0 0 1 24 7 Z" fill="#111"/></svg>
    <span class="clock">4:21 PM</span>
    <svg class="bt" width="16" height="26" viewBox="0 0 16 26"><path d="M2 7 L13 18 L8 23 V3 L13 8 L2 19" fill="none" stroke="#111" stroke-width="2"/></svg>
    <span class="level">100%</span>
    <svg class="battery" width="54" height="22" viewBox="0 0 54 22"><rect x="1" y="1" width="47" height="20" rx="3" fill="none" stroke="#111" stroke-width="2"/><rect x="4" y="4" width="41" height="14" rx="1" fill="#111"/><rect x="49" y="7" width="4" height="8" rx="1" fill="#111"/></svg>
  </div>

  <header class="app-header">
    <span class="brand-dot"></span>
    <span class="brand-name">QUELVORIN</span>
    <span class="company-name">COMPANY NAME</span>
  </header>

  <nav class="tabs">
    <div class="tab is-active">All News</div>
    <div class="tab">My News</div>
  </nav>

  <div class="panel-back"></div>
  <section class="news-panel">
    <article class="news-item" style="top:-30px">
      <div class="avatar" role="img" aria-label="Profile photo of Dana Frost" style="top:39px;background:radial-gradient(circle at 50% 45%,#a88470,#2a1e1c 70%)"></div>
      <div class="time" style="top:139px">2:30pm</div>
      <h2 class="name" style="top:52px;left:143px">Dana Frost</h2>
      <p class="excerpt" style="top:94px">Lorem Ipsum is simply dummy text of the printing and type-setting industry. Lorem Ipsum has been the industry's</p>
    </article>
    <article class="news-item" style="top:155px">
      <div class="avatar" role="img" aria-label="Profile photo of Lena Korvin" style="top:39px;background:radial-gradient(circle at 50% 45%,#c99a82,#6a4838 70%)"></div>
      <div class="time" style="top:145px">1:45pm</div>
      <h2 class="name" style="top:51px">Lena Korvin</h2>
      <p class="excerpt" style="top:102px">Lorem Ipsum is simply dummy text of the printing and type-setting industry. Lorem Ipsum has been the industry's</p>
    </article>
    <article class="news-item" style="top:339px">
      <div class="avatar" role="img" aria-label="Profile photo of Wes Stanton" style="top:40px;background:radial-gradient(circle at 50% 45%,#7a4e38,#2d2220 70%)"></div>
      <div class="time" style="top:145px">11:15am</div>
      <h2 class="name" style="top:52px">Wes Stanton</h2>
      <p class="excerpt" style="top:102px">Lorem Ipsum is simply dummy text of the printing and type-setting industry. Lorem Ipsum has been the industry's</p>
    </article>
    <article class="news-item" style="top:523px">
      <div class="avatar" role="img" aria-label="Profile photo of Noel Carter" style="top:38px;background:radial-gradient(circle at 50% 45%,#c4916e,#6e4a2e 70%)"></div>
      <div class="time" style="top:140px">9:40am</div>
      <h2 class="name" style="top:51px;left:154px">Noel Carter</h2>
      <p class="excerpt" style="top:102px">Lorem Ipsum is simply dummy text of the printing and type-setting industry. Lorem Ipsum has been the industry's</p>
    </article>
    <div class="scroll-track"></div>
    <div class="scroll-thumb"></div>
  </section>

  <footer class="tab-bar">
    <svg width="675" height="110" viewBox="0 0 675 110">
      <path d="M104 52 C150 52,150 64,184 64 C218 64,218 52,264 52 C310 52,310 64,343 64 C376 64,376 52,422 52 C468 52,468 64,502 64 C536 64,536 52,582 52" fill="none" stroke="var(--nav-ring)" stroke-width="20"/>
      <g fill="var(--nav-ring)">
        <circle cx="104" cy="52" r="41"/><circle cx="264" cy="52" r="41"/><circle cx="422" cy="52" r="41"/><circle cx="582" cy="52" r="41"/>
      </g>
      <g fill="var(--nav-face)">
        <circle cx="104" cy="52" r="30"/><circle cx="264" cy="52" r="30"/><circle cx="422" cy="52" r="30"/><circle cx="582" cy="52" r="30"/>
      </g>
      <g fill="var(--icon)">
        <path d="M84 53 L104 34 L124 53 L119 53 L119 70 L109 70 L109 59 L99 59 L99 70 L89 70 L89 53 Z"/>
        <circle cx="262" cy="54" r="18" fill="none" stroke="var(--icon)" stroke-width="4"/>
        <circle cx="262" cy="54" r="10" fill="none" stroke="var(--icon)" stroke-width="4"/>
        <circle cx="262" cy="54" r="3"/>
        <path d="M263 53 L282 34" stroke="var(--icon)" stroke-width="3"/>
        <path d="M278 32 L286 30 L284 38 Z"/>
        <path d="M404 60 L430 38 L440 64 L414 70 Z"/>
        <path d="M414 68 L420 78 L426 76 L422 66 Z"/>
        <path d="M440 40 Q446 46 444 54" fill="none" stroke="var(--icon)" stroke-width="3"/>
        <path d="M566 34 L586 34 L586 44 L582 44 L582 38 L578 38 L578 68 L582 68 L582 62 L586 62 L586 72 L566 72 Z"/>
        <path d="M566 34 L578 40 L578 74 L566 70 Z" opacity=".8"/>
        <path d="M584 48 L592 48 L592 42 L602 53 L592 64 L592 58 L584 58 Z"/>
      </g>
    </svg>
    <span class="label" style="left:20px">Home</span>
    <span class="label" style="left:188px">Objectives</span>
    <span class="label" style="left:337px">News</span>
    <span class="label" style="left:500px">Log Out</span>
  </footer>
</body>
</html>
```